Website for Apartment Rental in Prague

I would like to create designs of my website focused on luxury apartment rentals in Prague, Czech Republic. I created initial mock-ups, They are all attached. I need to design homepage and subpage. The mock-ups were created by combining elements from different websites that I liked but I need you to create a design that is unique and original. The attached files a only a guidance for the structure of the website but not for the design. Try to be creative.

Apartment

```html
<!DOCTYPE html>
<html lang="en">
<head>
<meta charset="utf-8">
<title>Residence Praha – Luxury Apartments</title>
<link href="https://fonts.googleapis.com/css2?family=Raleway:wght@300;400;500;600;700&display=swap" rel="stylesheet">
<style>
:root{
  --orange:#e3943a;
  --orange-light:#f2b467;
  --peach:#fcebd8;
  --ink:#333333;
  --muted:#8a8a8a;
  --line:#dedede;
  --white:#ffffff;
  --grey-bar:#d9d9d9;
}
*{box-sizing:border-box;margin:0;padding:0}
html,body{width:1200px;height:2928px;overflow:hidden}
body{font-family:'Raleway',sans-serif;color:var(--ink);background:var(--white);position:relative}

/* wordmark: one colour, one weight, plain square beside */
.wordmark{display:flex;align-items:center;gap:10px;font-weight:600;color:var(--white);line-height:1}
.wordmark i{display:block;width:12px;height:12px;background:var(--white)}

/* hero */
.hero{position:absolute;left:0;top:0;width:1200px;height:1112px}
.hero-photo{position:absolute;inset:0;background:linear-gradient(180deg,#3a2a20 0%,#7a5232 30%,#b07845 55%,#8b5a35 75%,#5c4030 100%)}
.hero-shade{position:absolute;inset:0;background:linear-gradient(180deg,rgba(0,0,0,.35) 0%,rgba(0,0,0,.05) 40%,rgba(0,0,0,0) 70%)}
.topbar{position:absolute;left:0;top:0;width:1200px;height:80px}
.logo{position:absolute;left:72px;top:30px;font-size:22px}
.utility{position:absolute;right:60px;top:30px;display:flex;gap:26px;font-size:14px;color:var(--white)}
.utility span+span::before{content:"|";margin-right:26px;opacity:.6}
.nav{position:absolute;left:60px;top:84px;width:1080px;height:40px;background:rgba(227,148,58,.9);display:flex;justify-content:space-between;align-items:center;padding:0 24px;font-size:15px;font-weight:600;color:var(--white)}
.hero-brand{position:absolute;top:300px;left:0;width:1200px;justify-content:center;font-size:62px;letter-spacing:3px}
.hero-brand i{width:18px;height:18px}
.hero-tag{position:absolute;top:392px;left:0;width:1200px;text-align:center;color:var(--white);font-size:40px;font-weight:500;letter-spacing:1px}
.hero-buttons{position:absolute;top:478px;left:0;width:1200px;display:flex;justify-content:center;gap:20px}
.btn{display:inline-block;padding:14px 30px;border-radius:30px;background:var(--white);color:var(--ink);font-size:15px;font-weight:700;letter-spacing:1px}

/* booking */
.booking{position:absolute;left:140px;top:880px;width:920px;height:220px}
.booking h2{text-align:center;font-size:40px;font-weight:600;color:var(--white);letter-spacing:1px}
.booking-rule{height:2px;background:rgba(255,255,255,.7);margin:10px 0 14px}
.field-row{display:flex;gap:16px;margin-bottom:10px}
.field{flex:1}
.field label{display:block;font-size:13px;color:var(--white);margin-bottom:4px}
.field div{height:34px;background:rgba(255,255,255,.85);border-radius:3px}
.field.small{flex:.5}
.field.action div{background:var(--orange-light);color:var(--ink);font-size:14px;font-weight:600;display:flex;align-items:center;justify-content:center}

/* vision */
.section-title{position:absolute;left:0;width:1200px;text-align:center;font-size:42px;font-weight:500;letter-spacing:1px;color:var(--ink)}
.intro{position:absolute;left:200px;width:800px;text-align:center;font-size:14px;line-height:20px;color:var(--muted)}
.features{position:absolute;left:120px;top:1338px;width:960px;display:flex;justify-content:space-between}
.feature{width:296px;height:100px;border:1px solid var(--line);display:flex;align-items:center;padding:0 18px;gap:16px;box-shadow:0 2px 6px rgba(0,0,0,.05)}
.feature h3{font-size:20px;font-weight:600;margin-bottom:4px}
.feature p{font-size:12px;line-height:16px;color:var(--muted)}

/* offers */
.offers{position:absolute;left:0;top:1520px;width:1200px;height:440px;background:var(--peach)}
.offers .section-title{top:50px}
.cards{position:absolute;left:80px;top:112px;width:1040px;display:flex;justify-content:space-between}
.card{width:236px;height:290px;background:var(--white);box-shadow:0 2px 8px rgba(0,0,0,.08)}
.card-photo{height:160px}
.card h4{font-size:17px;font-weight:700;line-height:21px;padding:14px 14px 6px}
.card .meta{font-size:11px;color:var(--muted);padding:0 14px;display:flex;gap:16px}
.card .details{margin:12px 14px 0;height:30px;background:var(--orange-light);border-radius:3px;display:flex;align-items:center;justify-content:center;font-size:13px;font-weight:700}
.arrow{position:absolute;top:228px;width:34px;height:34px;border-radius:50%;background:var(--white);box-shadow:0 1px 4px rgba(0,0,0,.15);display:flex;align-items:center;justify-content:center}

/* contact */
.contact{position:absolute;left:0;top:2290px;width:1200px;height:210px}
.contact-photo{position:absolute;inset:0;background:linear-gradient(180deg,#c9c9c9 0%,#8f8f8f 100%)}
.contact h2{position:absolute;top:34px;width:1200px;text-align:center;font-size:42px;font-weight:500;color:var(--white);letter-spacing:1px}
.contact p{position:absolute;top:92px;width:1200px;text-align:center;font-size:13px;color:var(--white)}
.contact-form{position:absolute;left:120px;top:136px;width:960px;display:flex;gap:18px}
.contact-form div{flex:1;height:40px;border-radius:20px;background:rgba(255,255,255,.9);font-size:13px;color:var(--muted);display:flex;align-items:center;padding-left:20px}
.contact-form .submit{flex:.6;background:var(--white);color:var(--ink);font-weight:700;justify-content:center;padding:0;font-size:15px}

/* footer */
.footer{position:absolute;left:0;top:2500px;width:1200px;height:348px;background:var(--orange);color:var(--white)}
.fcol{position:absolute;top:48px}
.fcol h5{font-size:18px;font-weight:600;margin-bottom:16px}
.fcol li{list-style:none;font-size:14px;line-height:26px}
.fcol li::before{content:"›";margin-right:8px}
.flogo .wordmark{font-size:20px}
.flogo p{margin-top:18px;font-size:13px;line-height:19px;width:200px}
.touch p{font-size:14px;line-height:22px;display:flex;gap:10px;align-items:flex-start;margin-bottom:8px}
.map{width:220px;height:180px}
.copyright{position:absolute;left:0;top:2848px;width:1200px;height:80px;background:var(--grey-bar);display:flex;align-items:center;justify-content:center;font-size:13px;color:#666}
</style>
</head>
<body>

<header class="hero">
  <div class="hero-photo" role="img" aria-label="Photograph of a luxury apartment living room with warm lighting"></div>
  <div class="hero-shade"></div>
  <div class="topbar">
    <div class="logo wordmark"><i></i>Residence Praha</div>
    <div class="utility"><span>Discover Prague</span><span>Our Hospitality</span><span>Club Us</span><span>Call Us Now</span></div>
  </div>
  <nav class="nav">
    <span>Home</span><span>Apartments</span><span>Services</span><span>Gallery</span><span>News</span><span>Exclusive Offers &amp; Tours</span><span>For Families</span><span>Contact</span>
  </nav>
  <div class="hero-brand wordmark"><i></i>RESIDENCE PRAHA</div>
  <div class="hero-tag">WE'LL HELP YOU FIND YOUR NEW HOME</div>
  <div class="hero-buttons"><span class="btn">FIND OUT MORE</span><span class="btn">BOOK AN APPOINTMENT</span></div>

  <section class="booking">
    <h2>OFFICIAL SITE - BEST PRICE GUARANTEED</h2>
    <div class="booking-rule"></div>
    <div class="field-row">
      <div class="field"><label>Check-in date</label><div></div></div>
      <div class="field"><label>Check-out date</label><div></div></div>
      <div class="field small"><label>Guests</label><div></div></div>
      <div class="field small"><label>Children</label><div></div></div>
    </div>
    <div class="field-row">
      <div class="field"><label>Promotional code</label><div></div></div>
      <div class="field small action"><label>&nbsp;</label><div>Check availability</div></div>
      <div class="field small action"><label>&nbsp;</label><div>Select Rental Unit</div></div>
    </div>
  </section>
</header>

<h2 class="section-title" style="top:1160px">A DIFFERENT VISION OF TRAVELLING</h2>
<p class="intro" style="top:1222px">Something special awaits you right in the heart of Europe. Steps from the Old Town, this stylish residence pairs refined comfort with quiet elegance, welcoming service and every convenience you need to feel at home. Experience the calm side of luxury in central Prague.</p>

<div class="features">
  <div class="feature">
    <svg width="44" height="44" viewBox="0 0 44 44" fill="none" stroke="#999" stroke-width="2"><path d="M8 20 L22 8 L36 20 V36 H8 Z"/><rect x="18" y="26" width="8" height="10"/></svg>
    <div><h3>APARTMENTS</h3><p>Stylish units to suit every stay, from cosy studios to large family suites.</p></div>
  </div>
  <div class="feature">
    <svg width="44" height="44" viewBox="0 0 44 44" fill="none" stroke="#999" stroke-width="2"><rect x="8" y="8" width="28" height="28" rx="3"/><path d="M14 22 L20 28 L30 16"/></svg>
    <div><h3>CHECK-OUT</h3><p>Easy check-out at any hour, with flexible late departures on request.</p></div>
  </div>
  <div class="feature">
    <svg width="44" height="44" viewBox="0 0 44 44" fill="none" stroke="#999" stroke-width="2"><circle cx="22" cy="22" r="14"/><path d="M22 14 V30 M17 18 H25 M17 26 H27"/></svg>
    <div><h3>RATES</h3><p>Fair nightly prices with all taxes and services included.</p></div>
  </div>
</div>

<section class="offers">
  <h2 class="section-title">EXCLUSIVE OFFERS</h2>
  <div class="cards">
    <div class="card"><div class="card-photo" role="img" aria-label="Photograph of a modern apartment interior" style="background:linear-gradient(135deg,#6b5444,#b08868)"></div><h4>Brand New Modern Apartment Location</h4><div class="meta"><span>2 Guests</span><span>1 Bedroom</span></div><div class="details">VIEW DETAILS</div></div>
    <div class="card"><div class="card-photo" role="img" aria-label="Photograph of a bright bedroom" style="background:linear-gradient(135deg,#8a6a4c,#d8b893)"></div><h4>Brand New Modern Apartment Location</h4><div class="meta"><span>4 Guests</span><span>2 Bedrooms</span></div><div class="details">VIEW DETAILS</div></div>
    <div class="card"><div class="card-photo" role="img" aria-label="Photograph of a living room with sofa" style="background:linear-gradient(135deg,#5a5047,#a59888)"></div><h4>Brand New Modern Apartment Location</h4><div class="meta"><span>3 Guests</span><span>1 Bedroom</span></div><div class="details">VIEW DETAILS</div></div>
    <div class="card"><div class="card-photo" role="img" aria-label="Photograph of a warm lounge area" style="background:linear-gradient(135deg,#9a6a3a,#e0a868)"></div><h4>Brand New Modern Apartment Location</h4><div class="meta"><span>6 Guests</span><span>3 Bedrooms</span></div><div class="details">VIEW DETAILS</div></div>
  </div>
  <div class="arrow" style="left:14px"><svg width="14" height="14" viewBox="0 0 14 14"><path d="M9 2 L4 7 L9 12" stroke="#666" stroke-width="2" fill="none"/></svg></div>
  <div class="arrow" style="right:14px"><svg width="14" height="14" viewBox="0 0 14 14"><path d="M5 2 L10 7 L5 12" stroke="#666" stroke-width="2" fill="none"/></svg></div>
</section>

<h2 class="section-title" style="top:2080px">INTERIORS DESIGNED BY MAISON VELA</h2>
<p class="intro" style="top:2150px;left:140px;width:920px">Every residence is shaped by the studio, with thoughtful layouts and carefully chosen materials in each room. Our spacious apartments and refined guest services have allowed us to set a new standard for private stays in the city. Years of experience and a passion for detail let us create homes that travellers and families remember and return to again and again.</p>

<section class="contact">
  <div class="contact-photo" role="img" aria-label="Photograph of the Prague skyline"></div>
  <h2>CONTACT US NOW</h2>
  <p>Send us a message and our team will reply within one day with answers, offers and ideas for your stay.</p>
  <div class="contact-form"><div>Name</div><div>Email</div><div>Other Detail</div><div class="submit">SUBMIT</div></div>
</section>

<footer class="footer">
  <div class="fcol flogo" style="left:84px"><div class="wordmark"><i></i>Residence Praha</div><p>Refined short and long stays in the historic heart of Prague, close to all the city offers.</p></div>
  <div class="fcol" style="left:340px"><h5>Quick Links</h5><ul><li>Home</li><li>About Us</li><li>Services</li><li>Gallery</li><li>News</li><li>Contact Us</li></ul></div>
  <div class="fcol touch" style="left:620px"><h5>Get In Touch</h5>
    <p><svg width="16" height="20" viewBox="0 0 16 20"><path d="M8 1 C4 1 1 4 1 8 C1 13 8 19 8 19 C8 19 15 13 15 8 C15 4 12 1 8 1Z" fill="#fff"/><circle cx="8" cy="8" r="2.5" fill="#e3943a"/></svg><span><b>RESIDENCE PRAHA</b><br>14 Lantern Lane, Praha 1<br>Czech Republic</span></p>
    <p><svg width="16" height="16" viewBox="0 0 16 16"><path d="M3 1 L6 1 L7 5 L5 6 C6 8 8 10 10 11 L11 9 L15 10 L15 13 C15 14 14 15 13 15 C6 15 1 10 1 3 C1 2 2 1 3 1Z" fill="#fff"/></svg><span>+420 555 010 200</span></p>
    <p><svg width="16" height="14" viewBox="0 0 16 14"><rect x="1" y="1" width="14" height="12" fill="none" stroke="#fff" stroke-width="1.6"/><path d="M1 1 L8 8 L15 1" fill="none" stroke="#fff" stroke-width="1.6"/></svg><span>stay@residencepraha.example</span></p>
  </div>
  <div class="fcol" style="left:900px"><h5>Map</h5><div class="map" role="img" aria-label="Map showing the residence location in Prague" style="background:linear-gradient(135deg,#e8eef2,#c6d6e2)"></div></div>
</footer>
<div class="copyright">© RESIDENCE PRAHA - 2017. All Rights Reserved.</div>

</body>
</html>
```